FREE DENTURES

The card will be placed on plastic stand at doctors office and Seniors centers. This is to acheive specific market segment of people that must have Senalto A & B card and FULL bluvoro.
The size of the card shuold be 3.1/2" X 6" printed on vertical format. The basic design must have a picture of a denture and a eye glass frame.The content should be:
NEED DENTURES and/or EYE GLASSES?
NO COST TO YOU
Must have SENALTO A & B and FULL BLUVORO
Must qualify for program
No obligation Call today
RUNO VASKA 555-283-6190
(Not affiliated with Harrowmere Federal Council, the Federal Senalto or the State Bluvoro Program

Add at a proper side or top. 2 stripes, 1 Red, 1 blue in a waive format.

```html
<!DOCTYPE html>
<html lang="en">
<head>
<meta charset="utf-8">
<title>No Cost Dentures and Eye Glasses – Rack Card</title>
<link rel="stylesheet" href="https://fonts.googleapis.com/css2?family=Archivo+Black&family=Carlito&family=Noto+Serif:wght@400;700&family=Roboto+Condensed:wght@400;700&family=Tinos:wght@400;700&display=swap">
<style>
  :root {
    --red: #e01f26;
    --blue: #0a55a0;
    --white: #ffffff;
    --ink: #1a1a1a;
    --border: #3a3a3a;
  }
  * { box-sizing: border-box; margin: 0; padding: 0; }
  html, body { width: 1200px; height: 973px; overflow: hidden; background: var(--white); }
  body { position: relative; font-family: "Noto Serif", serif; }

  .side-label {
    position: absolute; top: 30px;
    font: 400 22px "Carlito", sans-serif; color: var(--ink);
  }
  .side-label--front { left: 13px; }
  .side-label--back { left: 668px; }

  .card {
    position: absolute; top: 68px; width: 516px; height: 884px;
    border: 1px solid var(--border); overflow: hidden; background: var(--white);
  }
  .card--front { left: 14px; }
  .card--back { left: 668px; }

  .band { position: absolute; left: 0; width: 100%; }
  .band--top-red { top: 0; height: 33px; background: var(--red); }
  .band--top-blue { top: 33px; height: 35px; background: var(--blue); }
  .band--disclaimer {
    top: 806px; height: 37px; background: var(--blue);
    display: flex; align-items: center; justify-content: center;
    font: 400 12.5px "Roboto Condensed", sans-serif; color: var(--white); letter-spacing: -0.1px;
  }
  .band--bottom-red { top: 843px; height: 41px; background: var(--red); }
  .band--offer {
    top: 551px; height: 42px; background: var(--red);
    display: flex; align-items: center; justify-content: center;
    font: 400 33px "Archivo Black", sans-serif; color: var(--white); letter-spacing: 1px;
  }

  .hero-front { position: absolute; left: 0; top: 68px; }

  .question-badge { position: absolute; left: 50px; top: 388px; }
  .question-badge__text {
    position: absolute; left: 0; top: 0; width: 416px; height: 146px;
    display: flex; align-items: center; justify-content: center; text-align: center;
    font: 400 24px/1.35 "Tinos", serif; color: var(--white); letter-spacing: 0.5px;
  }

  .card-in-hand {
    position: absolute; left: 0; top: 599px; width: 196px; height: 132px;
    background: linear-gradient(135deg, #d9b9a0 0%, #c99e82 35%, #f3f1ee 55%, #e9edf3 100%);
    border-radius: 0 40px 40px 0;
  }

  .eligibility { position: absolute; text-align: center; font-weight: 700; color: var(--blue); }
  .eligibility .hl { color: var(--red); }
  .card--front .eligibility { left: 170px; width: 340px; top: 603px; font-size: 21px; line-height: 30px; }
  .card--back .eligibility { left: 140px; width: 360px; top: 628px; font-size: 24px; line-height: 34px; }

  .cta { position: absolute; left: 0; width: 100%; text-align: center; }
  .cta--call { top: 727px; font: 400 24px "Archivo Black", sans-serif; color: var(--blue); }
  .cta--contact { top: 761px; color: var(--red); font-family: "Archivo Black", sans-serif; white-space: nowrap; }
  .cta--contact .contact-name { font-size: 23px; }
  .cta--contact .contact-phone { font-size: 32px; margin-left: 8px; }

  .hero-back {
    position: absolute; left: 0; top: 68px; width: 100%; height: 483px;
    background:
      radial-gradient(ellipse 40% 50% at 72% 42%, #e9d3c6 0%, #dcc4b6 40%, rgba(230,233,238,0) 75%),
      radial-gradient(ellipse 30% 45% at 25% 55%, #dfe3ea 0%, rgba(240,242,246,0) 80%),
      linear-gradient(180deg, #eef1f5 0%, #e6e8ec 60%, #d9d1c0 100%);
  }
  .hero-back__copy { position: absolute; left: 22px; top: 82px; width: 210px; text-align: center; }
  .hero-back__question {
    font: 700 19px/1.3 "Tinos", serif; color: var(--blue);
    text-shadow: 1px 1px 0 var(--white), -1px -1px 0 var(--white), 1px -1px 0 var(--white), -1px 1px 0 var(--white);
  }
  .hero-back__call {
    margin-top: 10px; padding-left: 16px; text-align: left;
    font: 400 23px/1.25 "Archivo Black", sans-serif; color: var(--blue);
  }
  .hero-back__name { margin-top: 10px; font: 400 19px "Archivo Black", sans-serif; color: var(--red); }
  .hero-back__phone { font: 400 26px "Archivo Black", sans-serif; color: var(--red); }
</style>
</head>
<body>
  <div class="side-label side-label--front">Front</div>
  <div class="side-label side-label--back">Back</div>

  <section class="card card--front">
    <div class="band band--top-red"></div>
    <div class="band band--top-blue"></div>

    <svg class="hero-front" width="516" height="320" viewBox="0 0 516 320">
      <defs>
        <linearGradient id="heroFrontTone" x1="0" y1="0" x2="1" y2="1">
          <stop offset="0" stop-color="#e8dcd2"/>
          <stop offset="0.45" stop-color="#e2bfa6"/>
          <stop offset="1" stop-color="#cfb49e"/>
        </linearGradient>
      </defs>
      <path d="M0 0 H516 V200 Q258 400 0 200 Z" fill="url(#heroFrontTone)" role="img" aria-label="Photo of smiling seniors giving thumbs up"/>
      <path d="M0 200 Q258 400 516 200" fill="none" stroke="var(--blue)" stroke-width="5"/>
      <path d="M0 210 Q258 420 516 210" fill="none" stroke="var(--red)" stroke-width="6"/>
    </svg>

    <div class="question-badge">
      <svg width="416" height="146" viewBox="0 0 416 146">
        <ellipse cx="208" cy="73" rx="206" ry="66" fill="var(--red)"/>
        <ellipse cx="208" cy="73" rx="194" ry="74" fill="var(--white)"/>
        <ellipse cx="208" cy="73" rx="176" ry="68" fill="var(--blue)"/>
      </svg>
      <div class="question-badge__text">NEED DENTURES<br>AND OR<br>EYE GLASSES?</div>
    </div>

    <div class="band band--offer">NO COST TO YOU!!!</div>

    <div class="card-in-hand" role="img" aria-label="Photo of a hand holding a health insurance card"></div>
    <div class="eligibility">
      Must have:<br>
      <span class="hl">SENALTO A &amp; B</span><br>
      and <span class="hl">FULL BLUVORO</span><br>
      Must qualify for program
    </div>
    <div class="cta cta--call">No obligation Call today!</div>
    <div class="cta cta--contact"><span class="contact-name">Runo Vaska</span><span class="contact-phone">555-283-6190</span></div>

    <div class="band band--disclaimer">(Not affiliated with Harrowmere Federal Council, the Federal Senalto or the State Bluvoro Program)</div>
    <div class="band band--bottom-red"></div>
  </section>

  <section class="card card--back">
    <div class="band band--top-red"></div>
    <div class="band band--top-blue"></div>

    <div class="hero-back" role="img" aria-label="Photo of a smiling senior woman wearing glasses and a scarf"></div>
    <div class="hero-back__copy" style="top:150px;">
      <div class="hero-back__question">NEED DENTURES<br>AND OR<br>EYE GLASSES?</div>
      <div class="hero-back__call">No<br>obligation<br>Call today!</div>
      <div class="hero-back__name">Runo Vaska</div>
      <div class="hero-back__phone">555-283-6190</div>
    </div>

    <div class="band band--offer">NO COST TO YOU!!!</div>

    <div class="card-in-hand" role="img" aria-label="Photo of a hand holding a health insurance card"></div>
    <div class="eligibility">
      Must have:<br>
      <span class="hl">SENALTO A &amp; B</span><br>
      and <span class="hl">FULL BLUVORO</span><br>
      Must qualify for program
    </div>

    <div class="band band--disclaimer">(Not affiliated with Harrowmere Federal Council, the Federal Senalto or the State Bluvoro Program)</div>
    <div class="band band--bottom-red"></div>
  </section>
</body>
</html>
```